I am looking for a modern, clean and neat design for a reflexology and well being business. The business name is Gralo Tund (this is an old Latin word for wellbeing). The colours I would like are purple, white and grey. I am open to suggestions for pictures such as healing or working hands, a pair of feet, images that represent my business that you may think of....... or maybe you think no images at all would be best? My tag line is: "Relax, Renew, Revive" or "Find you balance......... Relax, Renew, Revive" I can decide which I want so I would like to see what both would look like. I would like space on the back to write the client's appointment date and time (more than once)

```html
<!DOCTYPE html>
<html lang="en">
<head>
<meta charset="utf-8">
<title>Gralo Tund – Business Cards</title>
<link href="https://fonts.googleapis.com/css2?family=Exo+2:wght@500&family=Lato:wght@400;700&display=swap" rel="stylesheet">
<style>
  :root {
    --purple: #9b00b4;
    --grey-dark: #444446;
    --grey-text: #3a3a3a;
    --grey-soft: #6a6a6c;
    --white: #ffffff;
    --paper-grey: #eeeeee;
    --backdrop: #e7e5e8;
  }
  * { box-sizing: border-box; margin: 0; padding: 0; }
  html, body { width: 1200px; height: 900px; overflow: hidden; }
  body {
    background: var(--backdrop);
    font-family: 'Lato', sans-serif;
    position: relative;
  }
  .card {
    position: absolute;
    width: 540px;
    height: 310px;
    background: var(--white);
    box-shadow: 0 6px 18px rgba(0,0,0,0.18);
    overflow: hidden;
  }
  .brand {
    display: flex;
    align-items: center;
    gap: 14px;
    font-family: 'Exo 2', sans-serif;
    font-weight: 500;
    letter-spacing: 1px;
    white-space: nowrap;
  }
  .brand-mark { border-radius: 50%; flex: none; }

  /* Appointment card */
  .appointment-card { left: 40px; top: 140px; }
  .appointment-card .header-band {
    height: 84px;
    background: var(--purple);
    display: flex;
    align-items: center;
    justify-content: center;
  }
  .appointment-card .brand { color: var(--white); font-size: 36px; }
  .appointment-card .brand-mark { width: 38px; height: 38px; background: var(--white); }
  .appointment-body { padding: 12px 40px 0; color: var(--grey-text); }
  .appointment-title {
    text-align: center;
    font-weight: 700;
    font-size: 20px;
    line-height: 1.2;
  }
  .appointment-title .accent { color: var(--purple); }
  .title-rule {
    border-bottom: 2px dotted var(--grey-text);
    margin: 4px 40px 0;
  }
  .field-row {
    display: flex;
    align-items: flex-end;
    gap: 8px;
    margin-top: 16px;
    font-weight: 700;
    font-size: 15px;
    line-height: 1;
    color: var(--purple);
    white-space: nowrap;
  }
  .field-line {
    flex: 1;
    border-bottom: 2px dotted var(--grey-text);
    height: 12px;
  }
  .field-line.short { flex: 0 0 110px; }
  .field-unit { font-weight: 400; font-size: 13px; }
  .notice {
    margin-top: 18px;
    font-weight: 700;
    font-size: 15px;
    text-align: center;
    white-space: nowrap;
  }
  .notice .accent { color: var(--purple); }

  /* Front card */
  .front-card { left: 620px; top: 440px; }
  .front-top {
    height: 150px;
    background: linear-gradient(180deg, #ffffff 0%, var(--paper-grey) 100%);
    display: flex;
    flex-direction: column;
    align-items: center;
    justify-content: center;
    gap: 8px;
  }
  .front-card .brand { color: var(--grey-dark); font-size: 44px; }
  .front-card .brand-mark { width: 52px; height: 52px; background: var(--purple); }
  .tagline {
    font-size: 15px;
    letter-spacing: 2px;
    color: var(--purple);
    font-weight: 700;
  }
  .divider { height: 6px; background: var(--grey-dark); }
  .divider-gap { height: 14px; background: var(--white); }
  .front-bottom {
    height: 140px;
    background: var(--purple);
    color: var(--white);
    display: flex;
    padding: 14px 30px 0 40px;
    gap: 30px;
  }
  .person { flex: 1; text-align: right; }
  .person-name { font-weight: 700; font-size: 23px; }
  .person-role { font-size: 16px; margin-bottom: 8px; }
  .person-address { font-size: 17px; line-height: 1.25; }
  .contact-list { list-style: none; font-size: 15px; }
  .contact-list li { display: flex; align-items: center; gap: 8px; height: 24px; white-space: nowrap; }
  .contact-icon {
    width: 16px; height: 16px;
    background: var(--white);
    border-radius: 2px;
    display: flex; align-items: center; justify-content: center;
  }
  .contact-icon svg { width: 12px; height: 12px; fill: var(--purple); stroke: var(--purple); }
</style>
</head>
<body>

  <section class="card appointment-card">
    <header class="header-band">
      <div class="brand"><span class="brand-mark"></span>Gralo Tund</div>
    </header>
    <div class="appointment-body">
      <h2 class="appointment-title">Your Next <span class="accent">Appointment on</span></h2>
      <div class="title-rule"></div>
      <div class="field-row">Name :<span class="field-line"></span></div>
      <div class="field-row">Date :<span class="field-line"></span>Time :<span class="field-line short"></span><span class="field-unit">AM / PM</span></div>
      <div class="field-row">Date :<span class="field-line"></span>Time :<span class="field-line short"></span><span class="field-unit">AM / PM</span></div>
      <div class="field-row">Date :<span class="field-line"></span>Time :<span class="field-line short"></span><span class="field-unit">AM / PM</span></div>
      <p class="notice">If unable to keep appointment, <span class="accent">kindly give 24hrs notice.</span></p>
    </div>
  </section>

  <section class="card front-card">
    <div class="front-top">
      <div class="brand"><span class="brand-mark"></span>Gralo Tund</div>
      <p class="tagline">Relax, Renew, Revive</p>
    </div>
    <div class="divider"></div>
    <div class="divider-gap"></div>
    <div class="front-bottom">
      <div class="person">
        <p class="person-name">Mara Velden</p>
        <p class="person-role">Managing Director</p>
        <p class="person-address">48 Linden Row<br>Harwick, 20417</p>
      </div>
      <ul class="contact-list">
        <li><span class="contact-icon"><svg viewBox="0 0 12 12"><path d="M2 1h2l1 3-1.5 1a6 6 0 0 0 3.5 3.5L8 7l3 1v2a1 1 0 0 1-1 1A9 9 0 0 1 1 2a1 1 0 0 1 1-1z"/></svg></span>555-018-2740</li>
        <li><span class="contact-icon"><svg viewBox="0 0 12 12"><rect x="2" y="1" width="8" height="3"/><rect x="1" y="5" width="10" height="6"/></svg></span>555-018-2741</li>
        <li><span class="contact-icon"><svg viewBox="0 0 12 12"><rect x="1" y="2.5" width="10" height="7" fill="none" stroke-width="1.4"/><path d="M1 2.5l5 4 5-4" fill="none" stroke-width="1.4"/></svg></span>hello@gralotund.com</li>
        <li><span class="contact-icon"><svg viewBox="0 0 12 12"><path d="M5 7l2-2M4.5 5.5L3 7a1.8 1.8 0 0 0 2.5 2.5L7 8M7.5 6.5L9 5a1.8 1.8 0 0 0-2.5-2.5L5 4" fill="none" stroke-width="1.4"/></svg></span>www.gralotund.com</li>
      </ul>
    </div>
  </section>

</body>
</html>
```